Birchwell Agency Condominium mail merge

We need a marketing proposal letter design to do a mail merge to potential e customers. We included our logo and an example of my miserable attempt to create a template. We are looking for a modern and attractive proposal template. Here is our website https://www.birchwellagency.example to be used for any additional information needed about us and our services.

Target Market(s)

New prospects

Industry/Entity Type

Insurance Agency

Requirements
Must have
• My project must have a modern professional look with merge fields similar to the file uploaded with this project.
Nice to have
• it would like have a condominium and a car icon graphic depicting there is additional discounts for both quotes bundled.
Should not have
• My project should not have any other logos or company name

```html
<!DOCTYPE html>
<html lang="en">
<head>
<meta charset="utf-8">
<title>Birchwell Agency – Condo Proposal Letter</title>
<link rel="stylesheet" href="https://fonts.googleapis.com/css2?family=Poppins:wght@400;500;600;700&family=Allura&display=swap">
<style>
  :root {
    --backdrop: #d9d9d9;
    --paper: #ffffff;
    --ink: #1a1a1a;
    --orange: #ed7d31;
    --peach: #f8cbad;
    --peach-light: #fbe4d5;
    --green: #3db54a;
    --alert: #e8151b;
    --rule: #222222;
  }
  * { box-sizing: border-box; margin: 0; padding: 0; }
  html, body {
    width: 1037px; height: 1200px; overflow: hidden;
    background: var(--backdrop);
    font-family: "Poppins", sans-serif;
    color: var(--ink);
  }
  .letter {
    position: absolute; left: 89px; top: 15px;
    width: 859px; height: 1170px;
    background: var(--paper);
  }
  .brand {
    position: absolute; left: 24px; top: 78px;
    display: flex; align-items: center; gap: 8px;
    font-size: 26px; font-weight: 600; color: var(--green);
  }
  .brand-mark { width: 18px; height: 18px; background: var(--orange); }
  .sender {
    position: absolute; right: 39px; top: 70px;
    text-align: right; font-size: 14.5px; line-height: 23.5px;
  }
  .sender .web { color: var(--orange); font-weight: 600; }
  .recipient {
    position: absolute; left: 34px; top: 185px;
    font-size: 14.5px; line-height: 24px;
  }
  .recipient .code { font-size: 17px; font-weight: 600; }
  .recipient .strong { font-size: 17px; font-weight: 600; }
  .recipient .first { margin-left: 5px; }
  .intro, .closing {
    position: absolute; left: 28px; width: 800px;
    font-size: 14.8px; line-height: 23.6px; letter-spacing: 0.5px;
  }
  .intro { top: 327px; }
  .closing { top: 786px; letter-spacing: 0; }
  .hl { color: var(--orange); font-weight: 600; }
  .quote {
    position: absolute; left: 28px; top: 449px;
    width: 800px; height: 261px;
    border: 1px solid var(--rule);
  }
  .merge-row { display: flex; height: 41px; border-bottom: 1px solid var(--rule); }
  .merge-row div {
    border-right: 1px solid var(--rule);
    text-align: center; font-weight: 700; font-size: 14px; padding-top: 2px;
  }
  .merge-row div:last-child { border-right: none; }
  .quote-body { position: absolute; left: 8px; top: 42px; right: 4px; bottom: 1px; display: flex; }
  .coverage { border-collapse: collapse; width: 522px; font-size: 14.5px; }
  .coverage td { padding: 0 8px; height: 24.3px; border-bottom: 1px solid #fff; vertical-align: top; line-height: 24px; }
  .coverage td:first-child { background: var(--orange); color: #fff; width: 261px; border-right: 1px solid #fff; }
  .coverage tr:nth-child(even) td:last-child { background: var(--peach); }
  .coverage tr:nth-child(odd) td:last-child { background: var(--peach-light); }
  .coverage th { background: var(--orange); color: #fff; text-align: left; padding: 0 8px; height: 24px; font-weight: 600; border-bottom: 1px solid #fff; }
  .coverage th:first-child { border-right: 1px solid #fff; }
  .coverage .tall td { height: 48px; }
  .coverage .bold td { font-weight: 700; }
  .premium {
    flex: 1; background: var(--orange); color: #fff; text-align: center;
    padding-top: 42px;
  }
  .premium h2 { font-size: 20px; line-height: 33px; font-weight: 600; }
  .premium p { font-size: 17px; margin-top: 2px; }
  .disclaimer {
    position: absolute; left: 28px; top: 721px; width: 790px;
    color: var(--alert); font-size: 12.5px; line-height: 21.5px;
  }
  .signoff { position: absolute; left: 28px; top: 900px; font-size: 14.5px; }
  .signature {
    position: absolute; left: 28px; top: 945px; width: 262px;
    font-family: "Allura", cursive; font-size: 50px; line-height: 60px;
    border-bottom: 2px solid var(--orange); white-space: nowrap;
  }
  .signer { position: absolute; left: 28px; top: 1013px; font-size: 16px; line-height: 26px; }
  .signer strong { font-weight: 600; font-size: 14.5px; }
  .bundle {
    position: absolute; left: 604px; top: 912px; width: 218px; height: 217px;
    background: var(--green); border-radius: 24px; color: #fff; text-align: center;
  }
  .bundle-art {
    margin: 26px auto 0; width: 196px; height: 96px; border-radius: 8px;
    background: linear-gradient(90deg, #f2efe9 0 50%, #f6d94a 50% 100%);
  }
  .bundle-text { margin-top: 18px; line-height: 1.15; }
  .bundle-text .small { font-size: 8px; }
  .bundle-text .site { font-size: 14px; font-weight: 700; }
  .bundle-text .big { font-size: 14px; font-weight: 700; }
</style>
</head>
<body>
<main class="letter">
  <div class="brand"><span class="brand-mark"></span>Birchwell Agency</div>

  <address class="sender" style="font-style:normal">
    2740 Harlow Park Road Ste. 310<br>
    Larkfield, FL 32099<br>
    <span class="web">BirchwellAgency.example</span>
  </address>

  <div class="recipient">
    <div class="code">&laquo;encodedimbno&raquo;</div>
    <div>&laquo;first_name1&raquo; &laquo;last_name1&raquo;</div>
    <div>&laquo;street_address1&raquo;</div>
    <div>&laquo;citystatezip&raquo; &laquo;<span class="strong">presorttrayid</span>&raquo;</div>
  </div>

  <p class="intro">We have saved our clients <span class="hl">$100s</span> on their Condo Insurance. Call us at <span class="hl">555-014-2270</span> so we can do the same for you! Bundle your Condo and Auto insurance together for additional savings with a multi-policy discount. Below is a sample Condo Insurance policy purchased recently in Orlando from Birchwell Insurance Agency.</p>

  <section class="quote">
    <div class="merge-row">
      <div style="width:179px">&lt;&lt;Address&gt;&gt;</div>
      <div style="width:210px">&lt;&lt;Address2&gt;&gt;</div>
      <div style="width:140px">&lt;&lt;City&gt;&gt;</div>
      <div style="width:140px">&lt;&lt;State&gt;&gt;</div>
      <div style="width:131px">&lt;&lt;Zip&gt;&gt;</div>
    </div>
    <div class="quote-body">
      <table class="coverage">
        <tr><th>Coverage</th><th>Limit</th></tr>
        <tr class="tall"><td>Increased Additional Living Expense</td><td>&lt;ColumnQ&gt;</td></tr>
        <tr><td>Loss Assessments</td><td>20%</td></tr>
        <tr><td>Family Liability Protection</td><td>$2,000</td></tr>
        <tr><td>Building Property Protection</td><td>$100,000</td></tr>
        <tr><td>Building Codes Coverages</td><td>&lt;ColumnK&gt;</td></tr>
        <tr class="bold"><td>All Perils Deductible</td><td>25%</td></tr>
        <tr class="bold"><td>Hurricane Deductible</td><td>$500</td></tr>
      </table>
      <div class="premium">
        <h2>Total Annual<br>Premium:</h2>
        <p><strong>&lt;&lt;</strong>Yearly Premium<strong>&gt;&gt;</strong></p>
      </div>
    </div>
  </section>

  <p class="disclaimer">*** The quoted premium is a sample premium based on a recent policy purchased in Orlando. Premium will differ based on information obtained on your application. ***</p>

  <p class="closing">If you are tired of paying too much for Condo Insurance and are wanting all of your insurance needs handled under one agency, then call us at <span class="hl">555-014-2270</span><strong>.</strong> One call is all it takes to see if you’ve got the right coverage at the right price.</p>

  <p class="signoff">Sincerely,</p>
  <div class="signature">Owen Birchwell</div>
  <div class="signer">[Owen Birchwell]<br><strong>Agency Principal</strong></div>

  <aside class="bundle">
    <div class="bundle-art" role="img" aria-label="Illustration of a condo house plus a yellow car, showing bundled coverage"></div>
    <div class="bundle-text">
      <div class="small">Switch your condo and car insurance to</div>
      <div class="site">BIRCHWELLAGENCY</div>
      <div class="small">to take advantage of</div>
      <div class="big">ADDITIONAL DISCOUNTS</div>
    </div>
  </aside>
</main>
</body>
</html>
```